Garlic Farm for Farm Sales/Restaurant sales

Need a professional, but appealing to agriculture world. We are selling 27 kinds of Organic Garlic from a farm in Simla,CO. I have uploaded logo and business information-we are going to need a template, because I will need to use it for four separate people.
-We are trying to appeal to Farm to table restaurants
-As well as growers/farmers

Target Market(s)

Agriculture Sales/Restaurants-Organic

Industry/Entity Type

Agriculture

Contact Information for Business Card

Want it to look more unique then your average kelto stock card- I want it to look amazing

Font styles to use
Sans Serif

Colors
0455a3
ec1f27
fbed22
ffffff

Requirements
Must have
• Just be creative
Nice to have
• Colorful
Should not have
• plain

```html
<!DOCTYPE html>
<html lang="en">
<head>
<meta charset="utf-8">
<title>Prairie Clove – Business Card</title>
<link href="https://fonts.googleapis.com/css2?family=Open+Sans:wght@400;600;700&display=swap" rel="stylesheet">
<style>
  :root {
    --navy: #0a2f63;
    --red: #c8202a;
    --white: #ffffff;
    --paper: #f5f3f4;
    --stage: #e9e7e3;
    --ink-light: #e8eef7;
  }
  * { box-sizing: border-box; margin: 0; padding: 0; }
  html, body { width: 1200px; height: 900px; overflow: hidden; }
  body {
    background: var(--stage);
    font-family: "Open Sans", Arial, sans-serif;
    position: relative;
  }
  .card {
    position: absolute;
    left: 290px;
    width: 620px;
    height: 354px;
    overflow: hidden;
    box-shadow: 0 6px 18px rgba(0,0,0,.15);
  }
  .card--back { top: 80px; background: var(--paper); }
  .card--front { top: 470px; background: var(--white); }

  .back__panel {
    position: absolute; left: 0; top: 0; bottom: 0;
    width: 228px; background: var(--navy);
  }
  .brand {
    position: absolute;
    display: flex; align-items: center; gap: 16px;
  }
  .brand__dot {
    width: 74px; height: 74px; border-radius: 50%;
    background: var(--red); flex: none;
  }
  .brand__text { line-height: 1.05; color: var(--navy); font-weight: 700; }
  .brand__name { font-size: 38px; letter-spacing: .5px; }
  .brand__tag { font-size: 15px; letter-spacing: 1px; }
  .card--back .brand { left: 191px; top: 140px; }
  .card--front .brand { left: 180px; top: 68px; }

  .front__band {
    position: absolute; left: 0; right: 0; bottom: 0;
    height: 148px; background: var(--navy); color: var(--ink-light);
  }
  .person {
    position: absolute; right: 28px; top: -58px;
    text-align: right; color: var(--navy);
  }
  .person__name { font-size: 17px; font-weight: 700; }
  .person__role { font-size: 13px; }
  .address {
    position: absolute; right: 28px; top: 14px;
    text-align: right; font-size: 13px; line-height: 1.45;
  }
  .contacts {
    position: absolute; left: 30px; top: 26px;
    list-style: none; font-size: 16px; line-height: 1.55;
  }
  .contacts li { display: flex; align-items: center; gap: 12px; }
  .contacts svg { width: 16px; height: 16px; fill: var(--ink-light); flex: none; }
</style>
</head>
<body>

<section class="card card--back" aria-label="Card back">
  <div class="back__panel"></div>
  <div class="brand">
    <span class="brand__dot"></span>
    <div class="brand__text">
      <div class="brand__name">prairie clove</div>
      <div class="brand__tag">organic garlic</div>
    </div>
  </div>
</section>

<section class="card card--front" aria-label="Card front">
  <div class="brand">
    <span class="brand__dot"></span>
    <div class="brand__text">
      <div class="brand__name">prairie clove</div>
      <div class="brand__tag">organic garlic</div>
    </div>
  </div>

  <div class="front__band">
    <div class="person">
      <div class="person__name">Daniel Hart</div>
      <div class="person__role">Managing Director</div>
    </div>
    <div class="address">1234, Address GoesHere,<br>Country, 12345</div>

    <ul class="contacts">
      <li>
        <svg viewBox="0 0 16 16" aria-hidden="true"><path d="M3 1h3l1.5 4-2 1.3a9 9 0 0 0 4.2 4.2L11 8.5l4 1.5v3a2 2 0 0 1-2 2A12 12 0 0 1 1 3a2 2 0 0 1 2-2z"/></svg>
        (055) 234 567 890
      </li>
      <li>
        <svg viewBox="0 0 16 16" aria-hidden="true"><path d="M4 1h7l2 2v3H4zM2 7h12a1 1 0 0 1 1 1v5h-3v2H4v-2H1V8a1 1 0 0 1 1-1zm3 4v3h6v-3z"/></svg>
        (055) 234567890
      </li>
      <li>
        <svg viewBox="0 0 16 16" aria-hidden="true"><path d="M1 3h14v10H1zm1.5 1.2L8 8.5l5.5-4.3z"/></svg>
        hello@prairieclove.com
      </li>
      <li>
        <svg viewBox="0 0 16 16" aria-hidden="true"><path d="M6.5 9.5l3-3 1 1-3 3zM4 8l2-2 1 1-2 2a1.4 1.4 0 0 0 2 2l2-2 1 1-2 2a2.8 2.8 0 0 1-4-4zm8 0l-2 2-1-1 2-2a1.4 1.4 0 0 0-2-2L7 7 6 6l2-2a2.8 2.8 0 0 1 4 4z"/></svg>
        www.prairieclove.com
      </li>
    </ul>
  </div>
</section>

</body>
</html>
```